We are a recruitment company based in Norwich/Cambridge England.
I have included our company logo which we want to remain the same.

What we are looking for is a new creative Business card which will really stand out!!

Contact Information for Business Card

Harriet Dunmore
email: Harriet@plavex.co.uk
Address: Brackwell House
Fenmoor Enterprise Park
Partridge Way
Norwich
QB9 3KX
Tel:01632 960418

```html
<!DOCTYPE html>
<html lang="en">
<head>
<meta charset="utf-8">
<title>Plavex Business Card</title>
<link rel="stylesheet" href="https://fonts.googleapis.com/css2?family=Montserrat:wght@600;700&family=Arimo:wght@400&display=swap">
<style>
  :root {
    --canvas: #2a2a2a;
    --green: #8cc43f;
    --green-soft: #97ca4d;
    --grey: #8a888c;
    --grey-dark: #6f6d72;
    --grey-faint: #f1f0f2;
    --white: #ffffff;
  }
  * { margin: 0; padding: 0; box-sizing: border-box; }
  html, body { width: 1200px; height: 880px; overflow: hidden; background: var(--canvas); }
  .canvas { position: relative; width: 1200px; height: 880px; }

  .card {
    position: absolute;
    width: 560px;
    height: 320px;
    border-radius: 22px;
    overflow: hidden;
  }

  /* Front */
  .card-front { left: 60px; top: 80px; background: var(--green); }
  .card-front .faint-mark {
    position: absolute; left: 150px; top: 20px;
    width: 280px; height: 280px; border-radius: 50%;
    background: var(--green-soft);
  }
  .front-brand {
    position: absolute; left: 0; right: 0; top: 110px;
    display: flex; align-items: center; justify-content: center; gap: 14px;
  }
  .brand-dot { width: 58px; height: 58px; border-radius: 50%; }
  .card-front .brand-dot { background: var(--white); }
  .brand-text { display: flex; flex-direction: column; }
  .brand-name {
    font-family: "Montserrat", sans-serif; font-weight: 700;
    font-size: 52px; line-height: 1; letter-spacing: -1px;
  }
  .brand-tag {
    font-family: "Arimo", sans-serif; font-size: 10px;
    letter-spacing: 3px; margin-top: 4px; padding-left: 4px;
  }
  .card-front .brand-name, .card-front .brand-tag { color: var(--white); }
  .front-web {
    position: absolute; left: 0; right: 0; top: 238px; text-align: center;
    font-family: "Arimo", sans-serif; font-size: 13px; letter-spacing: 3px;
    color: var(--white);
  }

  /* Back */
  .card-back { left: 580px; top: 470px; background: var(--white); }
  .card-back .faint-mark {
    position: absolute; left: 330px; top: -40px;
    width: 210px; height: 210px; border-radius: 50%;
    background: var(--grey-faint);
  }
  .back-brand {
    position: absolute; left: 32px; top: 52px;
    display: flex; align-items: center; gap: 12px;
  }
  .card-back .brand-dot { background: var(--green); width: 52px; height: 52px; }
  .card-back .brand-name { color: var(--grey); font-size: 46px; }
  .card-back .brand-tag { color: var(--grey); }
  .divider {
    position: absolute; left: 32px; right: 30px; top: 150px;
    height: 1px; background: var(--green);
  }
  .person { position: absolute; left: 32px; top: 164px; }
  .person-name {
    font-family: "Montserrat", sans-serif; font-weight: 700;
    font-size: 22px; color: var(--green); line-height: 1.1;
  }
  .person-role {
    font-family: "Arimo", sans-serif; font-size: 15px; color: var(--grey);
  }
  .contacts {
    position: absolute; left: 32px; top: 216px; list-style: none;
    font-family: "Arimo", sans-serif; font-size: 13px; color: var(--grey-dark);
  }
  .contacts li { display: flex; align-items: center; gap: 8px; height: 19px; }
  .contacts svg { width: 14px; height: 14px; }
  .address {
    position: absolute; right: 30px; top: 164px; text-align: right;
    font-family: "Arimo", sans-serif; font-size: 13px; line-height: 1.45;
    color: var(--grey-dark); font-style: normal;
  }
  .footer-band { position: absolute; left: 0; bottom: 0; width: 560px; height: 62px; }
</style>
</head>
<body>
<main class="canvas">

  <section class="card card-front" aria-label="Card front">
    <div class="faint-mark"></div>
    <div class="front-brand">
      <span class="brand-dot"></span>
      <div class="brand-text">
        <span class="brand-name">Plavex</span>
        <span class="brand-tag">Technology Recruitment</span>
      </div>
    </div>
    <p class="front-web">www.plavex.co.uk</p>
  </section>

  <section class="card card-back" aria-label="Card back">
    <div class="faint-mark"></div>
    <div class="back-brand">
      <span class="brand-dot"></span>
      <div class="brand-text">
        <span class="brand-name">Plavex</span>
        <span class="brand-tag">Technology Recruitment</span>
      </div>
    </div>
    <div class="divider"></div>

    <div class="person">
      <p class="person-name">Harriet Dunmore</p>
      <p class="person-role">CEO</p>
    </div>

    <ul class="contacts">
      <li>
        <svg viewBox="0 0 14 14"><circle cx="7" cy="7" r="6.2" fill="none" stroke="#8cc43f" stroke-width="1.2"/><rect x="5" y="3.5" width="4" height="7" rx="0.8" fill="none" stroke="#8cc43f" stroke-width="1"/></svg>
        01632 960418
      </li>
      <li>
        <svg viewBox="0 0 14 14"><circle cx="7" cy="7" r="6.2" fill="none" stroke="#8cc43f" stroke-width="1.2"/><rect x="3.8" y="4.8" width="6.4" height="4.4" fill="none" stroke="#8cc43f" stroke-width="1"/><path d="M3.8 4.8 L7 7.4 L10.2 4.8" fill="none" stroke="#8cc43f" stroke-width="1"/></svg>
        Harriet@plavex.co.uk
      </li>
      <li>
        <svg viewBox="0 0 14 14"><circle cx="7" cy="7" r="6.2" fill="#8cc43f"/><circle cx="7" cy="7" r="3.6" fill="none" stroke="#fff" stroke-width="0.9"/><path d="M3.4 7 H10.6 M7 3.4 V10.6" stroke="#fff" stroke-width="0.9"/></svg>
        www.plavex.co.uk
      </li>
    </ul>

    <address class="address">
      Brackwell House<br>
      Fenmoor Enterprise Park<br>
      Partridge Way<br>
      Norwich QB9 3KX
    </address>

    <svg class="footer-band" viewBox="0 0 560 62" aria-hidden="true">
      <path d="M0 48 L390 48 L400 38 L560 38 L560 62 L0 62 Z" fill="#8cc43f"/>
      <path d="M0 40 L386 40 L394 32 L394 38 L388 44 L0 44 Z" fill="#8a888c"/>
      <path d="M400 38 Q404 22 420 22 L560 22 L560 38 Z" fill="#8cc43f"/>
    </svg>
  </section>

</main>
</body>
</html>
```